Structural Engineering Business Card

Brookvane Drafting does residential house plans for clients in Central Florida. Would like simple but elegant business card that is appropriate for a house plan engineering company. Prefer black business card with black/white them but open to other shades of blue. I uploaded a sample card that I came across that looked good but please come up with your own creative designs.

Contact Information for Business Card

Name, Title, Phone, Email, Address, website

```html
<!DOCTYPE html>
<html lang="en">
<head>
<meta charset="utf-8">
<title>Brookvane Drafting — Business Card</title>
<link rel="stylesheet" href="https://fonts.googleapis.com/css2?family=Lato:wght@400;700;900&display=swap">
<style>
  :root {
    --page: #e9e7e4;
    --card: #1b1b1c;
    --ink: #ffffff;
    --ink-muted: #8a8a8c;
    --drawing-light: #4a4a4d;
    --drawing-mid: #333336;
  }
  * { box-sizing: border-box; margin: 0; padding: 0; }
  html, body {
    width: 1200px; height: 992px; overflow: hidden;
    background: var(--page);
    font-family: "Lato", sans-serif;
  }
  .canvas { position: relative; width: 1200px; height: 992px; }

  .card {
    position: absolute;
    width: 630px; height: 360px;
    background: var(--card);
    border-radius: 22px;
    overflow: hidden;
    box-shadow: 0 14px 30px rgba(0,0,0,0.28);
  }
  .card--back { left: 470px; top: 70px; }
  .card--front { left: 100px; top: 520px; }

  .plan-art {
    position: absolute;
    z-index: 0;
    background: radial-gradient(closest-side, var(--drawing-light) 0%, var(--drawing-mid) 45%, var(--card) 100%);
    opacity: 0.85;
  }
  .card--back .plan-art { left: 0; top: 0; width: 460px; height: 290px; }
  .card--front .plan-art { right: 0; bottom: 0; width: 340px; height: 250px; }

  .wordmark {
    position: absolute; z-index: 1;
    right: 30px; bottom: 34px;
    color: var(--ink);
    font-weight: 900;
    font-size: 30px;
    letter-spacing: 0.5px;
    text-transform: uppercase;
    line-height: 1.05;
    text-align: right;
  }

  .identity { position: absolute; z-index: 1; left: 44px; top: 46px; }
  .identity__name {
    color: var(--ink); font-weight: 700; font-size: 36px;
    letter-spacing: 0.5px; text-transform: uppercase; line-height: 1;
  }
  .identity__title { color: var(--ink-muted); font-size: 22px; margin-top: 6px; }
  .identity__rule { width: 44px; height: 3px; background: var(--ink); margin-top: 16px; }

  .contact { position: absolute; z-index: 1; left: 44px; top: 178px; list-style: none; }
  .contact__item {
    display: flex; align-items: flex-start; gap: 12px;
    color: var(--ink); font-size: 19px; line-height: 1.2;
    margin-bottom: 7px;
  }
  .contact__icon { flex: 0 0 22px; width: 22px; height: 22px; margin-top: 1px; }
</style>
</head>
<body>
<div class="canvas">

  <section class="card card--back" aria-label="Card back">
    <div class="plan-art" role="img" aria-label="Faint architectural floor plan drawing with circular rotunda and trees"></div>
    <div class="wordmark">Brookvane<br>Drafting</div>
  </section>

  <section class="card card--front" aria-label="Card front">
    <div class="plan-art" role="img" aria-label="Faint architectural floor plan drawing with rooms, trees and circular rotunda"></div>

    <div class="identity">
      <h1 class="identity__name">Daniel Hargrove</h1>
      <p class="identity__title">Founder &amp; CEO</p>
      <div class="identity__rule"></div>
    </div>

    <ul class="contact">
      <li class="contact__item">
        <svg class="contact__icon" viewBox="0 0 22 22" aria-hidden="true">
          <circle cx="11" cy="11" r="11" fill="#fff"/>
          <path d="M7.5 6.2c.5-.4 1.1-.3 1.4.2l1 1.6c.3.5.2 1-.2 1.3l-.6.5c.5 1.1 1.3 1.9 2.4 2.4l.5-.6c.3-.4.9-.5 1.3-.2l1.6 1c.5.3.6.9.2 1.4l-.7.8c-.6.6-1.6.7-2.6.2-2.2-1.1-3.9-2.8-5-5-.5-1-.4-2 .2-2.6z" fill="#1b1b1c"/>
        </svg>
        <span>(123) 456-7890</span>
      </li>
      <li class="contact__item">
        <svg class="contact__icon" viewBox="0 0 22 22" aria-hidden="true">
          <circle cx="11" cy="11" r="11" fill="#fff"/>
          <rect x="5.5" y="7" width="11" height="8" rx="1" fill="#1b1b1c"/>
          <path d="M6 7.5l5 4 5-4" stroke="#fff" stroke-width="1.1" fill="none"/>
        </svg>
        <span>office@brookvane.com</span>
      </li>
      <li class="contact__item">
        <svg class="contact__icon" viewBox="0 0 22 22" aria-hidden="true">
          <circle cx="11" cy="11" r="11" fill="#fff"/>
          <circle cx="11" cy="11" r="5.5" fill="none" stroke="#1b1b1c" stroke-width="1.4"/>
          <ellipse cx="11" cy="11" rx="2.3" ry="5.5" fill="none" stroke="#1b1b1c" stroke-width="1.1"/>
          <path d="M5.5 11h11" stroke="#1b1b1c" stroke-width="1.1"/>
        </svg>
        <span>www.brookvane.com</span>
      </li>
      <li class="contact__item">
        <svg class="contact__icon" viewBox="0 0 22 22" aria-hidden="true">
          <circle cx="11" cy="11" r="11" fill="#fff"/>
          <path d="M11 4.8a4 4 0 0 0-4 4c0 3 4 7.8 4 7.8s4-4.8 4-7.8a4 4 0 0 0-4-4z" fill="#1b1b1c"/>
          <circle cx="11" cy="8.8" r="1.5" fill="#fff"/>
        </svg>
        <span>Your Address, City<br>State, Zip 1235</span>
      </li>
    </ul>
  </section>

</div>
</body>
</html>
```